San Francisco Leading Consulting firm - 47Vora Web Design Project

•Create a Web Design
•Uncoded webpage layout design
•2 Pages Design - Homepage + Interior Page

Task Description
Hello, we're looking for a re-design our current website www.47vora-example.com

we have a sample mockup design @

http://47vora.pubtrellis-example.org/

This shows the layout that we like and also a sample of 6 pictures that would change based on where you mouse over..

6 pictures HOME design needs to be included.

SMART
THOUGHTFUL
FLEXIBLE
CREATIVE SERVICES
TECHNICAL SERVICES
PARTNERS

sites we like:

http://www.melvanadvisory-example.com/Home.cfm?id=Home
http://www.plinthworks-example.com/index.html

Our company can be best described as: 100+ employees, cutting-edge, depandable, innovative, strong, smart.

Our Primary focus is: IT Consulting Services and Creative Design services

47Vora LLC is a consulting firm providing creative design, business and technology solutions to both private and public interests.

Established in 1996, 47Vora is a San Francisco based company providing specialists for a range of business needs including:

Creative Design Services
•Print
•Logo Design
•Website Design
•Illustration

and

Business and Technology solutions

•Application Software and Web Development
•Business Process Re-Design (BPR)
•Business/Systems Analysis and Requirement Documentation
•Mentoring and Training
•Network/Hardware Installation Services
•System Design and Architecture
•Vendor Management
•Docuvault Architecture and Implementation

our sample mockup site:

Reason: Due to holiday season, we're not available to work with designers and finilize our design.  

Thank you very much for submitting your design.

We appreciate your time and creativity.   Since, our office is currently closed for holidays, we will be reviewing it in details next week and will make our decision as soon as possible.

It would be great if you could submit any of your changes by Wed next week, so it would be part of our reviews. 

Please see updated wireframe under attachments:  we have some minor updates to our wireframe that we would like you to update your designs, if possible.  

We also encorouge you not to use our standard wireframe and come up with more unique designs.   Everything would be considered when we review your design.

 

Target Market(s)

Creative services and professional services clients, including government agencies

Industry/Entity Type

Business

Requirements
Must have
• Clean, professional look, easy navigation

```html
<!DOCTYPE html>
<html lang="en">
<head>
<meta charset="utf-8">
<title>47Vora — Home</title>
<link href="https://fonts.googleapis.com/css2?family=Arimo:wght@400;700&family=Didact+Gothic&display=swap" rel="stylesheet">
<style>
  :root {
    --backdrop: #a3a3a3;
    --page: #ffffff;
    --nav: #8e8e8e;
    --nav-rule: #d8d8d8;
    --accent: #e01b22;
    --ink: #555555;
    --ink-soft: #666666;
    --ink-dark: #222222;
    --divider: #cfcfcf;
    --caption-band: rgba(110, 110, 110, 0.82);
  }
  * { box-sizing: border-box; margin: 0; padding: 0; }
  html, body {
    width: 1200px; height: 900px; overflow: hidden;
    background: var(--backdrop);
    font-family: "Arimo", Arial, sans-serif;
  }
  .site {
    position: relative; width: 1200px; height: 900px;
  }
  .page {
    position: absolute; left: 40px; top: 40px; width: 1120px; height: 780px;
    background: var(--page);
  }
  .brand {
    position: absolute; left: 22px; top: 36px;
    display: flex; align-items: center; gap: 12px;
  }
  .brand-dot {
    width: 40px; height: 40px; border-radius: 50%; background: var(--accent);
  }
  .brand-name {
    font-size: 40px; font-weight: 400; color: var(--ink-dark); letter-spacing: 1px;
  }
  .login {
    position: absolute; right: 28px; top: 20px;
    background: var(--nav); color: #fff; font-size: 13px; font-weight: 700;
    padding: 4px 8px; text-decoration: none;
  }
  .main-nav {
    position: absolute; left: 16px; top: 124px; width: 1074px; height: 30px;
    background: var(--nav); display: flex;
  }
  .main-nav a {
    color: #fff; text-decoration: none; font-size: 17px;
    line-height: 30px; padding: 0 16px;
    border-right: 2px solid var(--nav-rule);
  }
  .nav-rule {
    position: absolute; left: 16px; top: 154px; width: 1074px; height: 5px;
    background: var(--accent);
  }
  .slide-picker {
    position: absolute; left: 24px; top: 172px; display: flex; gap: 2px;
  }
  .slide-picker span {
    width: 22px; height: 22px; border: 2px solid #444; background: #fff;
  }
  .slide-picker span.is-active { background: #333; }
  .hero {
    position: absolute; left: 16px; top: 200px; width: 1078px; height: 290px;
  }
  .hero-photo {
    position: absolute; inset: 0;
    background: radial-gradient(ellipse at 62% 45%, #e9d2cf 0%, #f3eceb 30%, #ffffff 65%);
  }
  .hero-caption {
    position: absolute; left: 0; bottom: 0; width: 100%; height: 64px;
    background: var(--caption-band); color: #fff;
    font-family: "Didact Gothic", "Century Gothic", sans-serif;
    font-size: 40px; line-height: 64px; padding-left: 24px; letter-spacing: -0.3px;
  }
  .hero-caption strong { font-family: "Arimo", Arial, sans-serif; font-weight: 700; }
  .features {
    position: absolute; left: 0; top: 476px; width: 1120px; height: 284px;
  }
  .feature {
    position: absolute; top: 0; width: 362px; height: 284px; padding: 20px 0 0 40px;
  }
  .feature + .feature { border-left: 1px solid var(--divider); }
  .feature:nth-child(1) { left: 0; }
  .feature:nth-child(2) { left: 334px; padding-left: 30px; }
  .feature:nth-child(3) { left: 696px; padding-left: 30px; }
  .feature-audience { font-size: 15px; color: var(--ink-soft); }
  .feature-title { font-size: 30px; font-weight: 400; color: var(--ink); margin: 22px 0 12px; }
  .feature-text { font-size: 15px; line-height: 22px; color: var(--ink-soft); width: 280px; }
  .learn-more {
    display: inline-flex; align-items: center; gap: 8px; margin-top: 14px;
    font-size: 16px; font-weight: 700; color: var(--ink); text-decoration: none;
  }
  .copyright {
    position: absolute; left: 54px; top: 846px; font-size: 12px; color: #555;
  }
</style>
</head>
<body>
<div class="site">
  <div class="page">
    <div class="brand">
      <span class="brand-dot"></span>
      <span class="brand-name">47VORA</span>
    </div>
    <a class="login" href="#">Login</a>

    <nav class="main-nav">
      <a href="#">COMPANY</a>
      <a href="#">TECHNICAL SERVICES</a>
      <a href="#">CREATIVE SERVICES</a>
      <a href="#">PARTNERS</a>
      <a href="#">CONTACT US</a>
    </nav>
    <div class="nav-rule"></div>

    <div class="slide-picker">
      <span></span><span class="is-active"></span><span></span><span></span><span></span><span></span>
    </div>

    <section class="hero">
      <div class="hero-photo" role="img" aria-label="Woman in a red top doing a deep seated yoga stretch on a white background"></div>
      <p class="hero-caption"><strong>Flexible:</strong> the world moves too fast for rigid solutions.</p>
    </section>

    <section class="features">
      <article class="feature">
        <p class="feature-audience">for graphic designers</p>
        <h2 class="feature-title">Get Creative!</h2>
        <p class="feature-text">47Vora is looking for top creative talent to deliver graphic design solutions for some leading global brands Do you have what it takes?</p>
        <a class="learn-more" href="#">Learn More
          <svg width="10" height="12" viewBox="0 0 10 12"><path d="M0 0 L10 6 L0 12 Z" fill="#e01b22"/></svg></a>
      </article>
      <article class="feature">
        <p class="feature-audience">for clients</p>
        <h2 class="feature-title">The 47Vora Difference</h2>
        <p class="feature-text">Smart, Flexible, Thoughtful: find out why leading corporations and government agencies are turning to 47vora to help manage their most demanding IT services challenges.</p>
        <a class="learn-more" href="#">Learn More
          <svg width="10" height="12" viewBox="0 0 10 12"><path d="M0 0 L10 6 L0 12 Z" fill="#e01b22"/></svg></a>
      </article>
      <article class="feature">
        <p class="feature-audience">for partners</p>
        <h2 class="feature-title">Team Up With the Best</h2>
        <p class="feature-text">When it comes to technology partnerships, our mission it so make you a success.</p>
        <a class="learn-more" href="#">Learn More
          <svg width="10" height="12" viewBox="0 0 10 12"><path d="M0 0 L10 6 L0 12 Z" fill="#e01b22"/></svg></a>
      </article>
    </section>
  </div>
  <p class="copyright">Copyright 2010, 47Vora, LLC All rights reserved.</p>
</div>
</body>
</html>
```